Corportate Power Point Template

We need a corporate PPT Design for our startup Big Data company.

Basically, our company will ingest, analyze and generate dynamic Dashboards with data consumed from different sources like Social Networks, Enterprise Legacy Systems such as e-Commerce, ERP, CRM and others.

Company is headquartered in Brazil, but will have a global presence.

Industry/Entity Type

It Company

```html
<!DOCTYPE html>
<html lang="en">
<head>
<meta charset="utf-8">
<title>Project Title Here</title>
<link rel="stylesheet" href="https://fonts.googleapis.com/css2?family=Open+Sans:wght@600;700&family=Saira+Semi+Condensed:wght@400;500;600&display=swap">
<style>
  :root {
    --orange: #ff7a35;
    --orange-soft: #fde3d2;
    --ink: #3b3b3b;
    --ink-dark: #333333;
    --row-grey: #e6e7e9;
    --rule: #e4e0dd;
    --white: #ffffff;
  }
  * { margin: 0; padding: 0; box-sizing: border-box; }
  html, body { width: 1200px; height: 900px; overflow: hidden; }
  body {
    position: relative;
    background: #fffdfc;
    font-family: "Saira Semi Condensed", "Arial Narrow", sans-serif;
    color: var(--ink);
  }
  .backdrop-pattern {
    position: absolute; inset: 0;
    background:
      radial-gradient(ellipse 520px 300px at 250px 120px, rgba(253,214,190,0.55), rgba(255,255,255,0) 75%),
      radial-gradient(ellipse 420px 520px at 1120px 300px, rgba(240,234,232,0.7), rgba(255,255,255,0) 75%),
      radial-gradient(ellipse 500px 300px at 1100px 800px, rgba(253,226,208,0.45), rgba(255,255,255,0) 75%);
  }
  .title-accent {
    position: absolute; left: 0; top: 33px;
    width: 12px; height: 75px;
    background: var(--orange);
  }
  .slide-title {
    position: absolute; left: 34px; top: 26px;
    font-size: 60px; font-weight: 600; line-height: 1.3;
    color: var(--ink);
  }
  .slide-title .highlight { color: var(--orange); }
  .intro {
    position: absolute; left: 72px; top: 190px; width: 1060px;
    font-size: 22.5px; font-weight: 500; line-height: 39px;
    color: var(--ink);
  }
  .table-card {
    position: absolute; left: 69px; top: 303px;
    width: 1075px; height: 393px;
    background: var(--white);
    box-shadow: 0 0 6px rgba(0,0,0,0.22);
  }
  .data-table {
    position: absolute; left: 9px; top: 12px; width: 1054px;
    font-family: "Open Sans", Arial, sans-serif;
  }
  .data-row {
    position: relative; height: 62px;
    display: flex; align-items: center;
    background: var(--row-grey);
    margin-top: 15px;
    font-size: 19.5px; font-weight: 600; color: var(--ink-dark);
  }
  .data-row.header {
    height: 61px; margin-top: 0;
    background: var(--orange); color: var(--white);
    font-size: 22.5px; font-weight: 700;
  }
  .data-row.header + .data-row { margin-top: 12px; }
  .cell { position: absolute; white-space: nowrap; }
  .cell.c1 { left: 25px; }
  .cell.c2 { left: 369px; }
  .cell.c3 { left: 729px; }
  .footer-rule {
    position: absolute; left: 0; top: 817px; width: 1200px; height: 1px;
    background: var(--rule);
  }
  .presenter {
    position: absolute; left: 12px; top: 850px;
    font-size: 20px; font-weight: 400; color: var(--ink-dark);
  }
  .presenter .name { color: var(--orange); }
  .brand {
    position: absolute; right: 16px; top: 842px;
    display: flex; align-items: center; gap: 10px;
    font-size: 34px; font-weight: 500; color: var(--orange); line-height: 1;
  }
  .brand-square { width: 22px; height: 22px; background: var(--orange); }
</style>
</head>
<body>
  <div class="backdrop-pattern" role="img" aria-label="Soft orange and grey abstract background texture"></div>

  <div class="title-accent"></div>
  <h1 class="slide-title"><span class="highlight">Project</span> Title Here</h1>

  <p class="intro">Lorem ipsum dolor sit ipsum Lorem ipsum dolor sit ipsum Lorem ipsum Lorem ipsum dolor sit ipsum Lorem ipsum dolor sit ipsum Lorem ipsum</p>

  <section class="table-card">
    <div class="data-table">
      <div class="data-row header">
        <span class="cell c1">Content Title Here</span>
        <span class="cell c2">Content Title Here</span>
        <span class="cell c3">Content Title Here</span>
      </div>
      <div class="data-row">
        <span class="cell c1">Lorem ipsum dolor Lorem ipsum</span>
        <span class="cell c2">Lorem ipsum dolor Lorem ipsum</span>
        <span class="cell c3">Lorem ipsum dolor Lorem ipsum</span>
      </div>
      <div class="data-row">
        <span class="cell c1">Lorem ipsum dolor Lorem ipsum</span>
        <span class="cell c2">Lorem ipsum dolor Lorem ipsum</span>
        <span class="cell c3">Lorem ipsum dolor Lorem ipsum</span>
      </div>
      <div class="data-row">
        <span class="cell c1">Lorem ipsum dolor Lorem ipsum</span>
        <span class="cell c2">Lorem ipsum dolor Lorem ipsum</span>
        <span class="cell c3">Lorem ipsum dolor Lorem ipsum</span>
      </div>
      <div class="data-row">
        <span class="cell c1">Lorem ipsum dolor Lorem ipsum</span>
        <span class="cell c2">Lorem ipsum dolor Lorem ipsum</span>
        <span class="cell c3">Lorem ipsum dolor Lorem ipsum</span>
      </div>
    </div>
  </section>

  <div class="footer-rule"></div>
  <p class="presenter">Persentatator Name : <span class="name">Marcos Teixeira</span></p>
  <div class="brand">
    <span class="brand-square"></span>
    <span class="brand-name">Brightline Data</span>
  </div>
</body>
</html>
```